Business card design for a dynamic IT consulting company

We need a business card design for a young firm, specialized in the Telecommunications/Consulting industry. The name of the company is Quindor and Partners Business Consulting Ltd. (Short name: Quindor and Partnes)
Quindor = solve read reverse, so we aim to be uncomplicated and solution-oriented. The small pipe in our logo is also related to the word solve. So we need a new business card design, which is simple, eye catching and something non traditional (I would probably prefer a square shaped design rather than a rectangle, but open for suggestions). Attached our logo.

Target Market(s)

Usually our customers are Tier1 Telecoms providers (Q-Netra, Palorix, etc) and their executives.

Industry/Entity Type

Business

Contact Information for Business Card

Name: Bence Tolnavari
Email: b.tolnavari@quindor.hu
Web: www.quindor.hu
Mobile: +36 30 518 2769
Title: Managing Director

Optional:
Company name: Quindor and Partners Ltd.
Address: 1087 Budapest, Tolvenka str. 28/C, Hungary

Font styles to use
Other font styles liked:
• helveticaneue_medium, Prime Regular are used now.

Colors

Designer to choose colors to be used in the design.

Requirements
Must have
• I would like to have a 2 sided design.
Nice to have
• I thought if we make the logo a bit bigger (without the company name), that could go to the back with the company name below. I though, if the pipe in the logo is somehow touchable on the business card, would be nice and unique.

```html
<!DOCTYPE html>
<html lang="en">
<head>
<meta charset="utf-8">
<title>Quindor and Partners – Business Card</title>
<link rel="stylesheet" href="https://fonts.googleapis.com/css2?family=Open+Sans:wght@400;600;700&display=swap">
<style>
  :root {
    --bg: #ebebeb;
    --paper: #fbfbfb;
    --brand-blue: #009ddc;
    --ink: #3a3a3a;
    --ink-soft: #555555;
    --logo-grey: #5a5a5a;
    --white: #ffffff;
  }
  * { box-sizing: border-box; margin: 0; padding: 0; }
  html, body {
    width: 1200px; height: 900px; overflow: hidden;
    background: var(--bg);
    font-family: "Open Sans", Arial, sans-serif;
  }
  .canvas {
    position: relative; width: 1200px; height: 900px;
    display: flex; align-items: center; justify-content: center; gap: 60px;
  }
  .card {
    position: relative;
    width: 504px; height: 288px;
    box-shadow: 0 10px 24px rgba(0,0,0,.12), 0 2px 4px rgba(0,0,0,.08);
  }
  .card--front { background: var(--paper); color: var(--ink); }
  .card--back { background: var(--brand-blue); }

  .holder { position: absolute; left: 30px; top: 26px; }
  .holder__name {
    font-weight: 700; font-size: 14px; letter-spacing: .02em;
    color: var(--brand-blue); text-transform: uppercase;
  }
  .holder__title { font-size: 11px; color: var(--ink-soft); margin-top: 1px; }

  .contacts { position: absolute; left: 30px; top: 112px; width: 165px; list-style: none; }
  .contacts li {
    display: flex; align-items: center; gap: 7px;
    font-size: 11px; line-height: 18px; color: var(--ink);
    white-space: nowrap;
  }
  .contacts svg { width: 10px; height: 10px; fill: var(--brand-blue); flex: none; }

  .wordmark {
    display: flex; align-items: center; gap: 10px;
    font-weight: 600; letter-spacing: .01em; white-space: nowrap;
  }
  .wordmark__square { width: 16px; height: 16px; flex: none; }
  .card--front .wordmark {
    position: absolute; left: 214px; top: 96px;
    font-size: 24px; color: var(--logo-grey);
  }
  .card--front .wordmark__square { background: var(--brand-blue); width: 14px; height: 14px; }
  .card--back .wordmark {
    position: absolute; left: 50%; top: 50%;
    transform: translate(-50%, -50%);
    font-size: 30px; color: var(--white);
  }
  .card--back .wordmark__square { background: var(--white); width: 18px; height: 18px; }

  .company { position: absolute; right: 30px; bottom: 24px; text-align: right; font-size: 11px; line-height: 15px; }
  .company__name { color: var(--brand-blue); }
  .company__address { color: var(--ink); }
</style>
</head>
<body>
<main class="canvas">
  <section class="card card--front" aria-label="Business card front">
    <div class="holder">
      <div class="holder__name">Bence Tolnavari</div>
      <div class="holder__title">Managing Director</div>
    </div>

    <ul class="contacts">
      <li>
        <svg viewBox="0 0 10 10" aria-hidden="true"><path d="M2 0.5h2l.8 2.3-1.3.9a5.5 5.5 0 0 0 2.8 2.8l.9-1.3 2.3.8v2c0 .6-.5 1-1 1A8.5 8.5 0 0 1 1 1.5c0-.6.4-1 1-1z"/></svg>
        +36 30 518 2769
      </li>
      <li>
        <svg viewBox="0 0 10 10" aria-hidden="true"><rect x="0.5" y="2" width="9" height="6" rx="0.6"/></svg>
        b.tolnavari@quindor.hu
      </li>
      <li>
        <svg viewBox="0 0 10 10" aria-hidden="true"><circle cx="5" cy="5" r="4.6"/></svg>
        www.quindor.hu
      </li>
    </ul>

    <div class="wordmark">
      <span class="wordmark__square" aria-hidden="true"></span>
      <span>Quindor &amp; Partners</span>
    </div>

    <div class="company">
      <div class="company__name">Quindor and Partners Ltd.</div>
      <div class="company__address">1087 Budapest, Tolvenka<br>str. 28/C, Hungary</div>
    </div>
  </section>

  <section class="card card--back" aria-label="Business card back">
    <div class="wordmark">
      <span class="wordmark__square" aria-hidden="true"></span>
      <span>Quindor &amp; Partners</span>
    </div>
  </section>
</main>
</body>
</html>
```